Gazebo 3x3m design

I would require design/branding for Gazebo with size 3x3 meters for company called Up The Lane. This would be for Korean style Con Dogs using attached already designed cartoon characters (corn dog and cake Up The Lane), but making design to stand out, attractive and eye catching. Design requires to cover these as per attached example of different style of Gazebo branding:

Use attached characters with wording Up The Lane Korean Corn Dogs & Lovelies (not & more)
2x 2 meter high and 3 meter wide walls
2x 1 meter high and 3 meter wide half walls
1x canopy design (exact measurements in API file will be sent to the final designer)

The font with the cartoon Characters is not necessary required. Please provide font that Suits your design best. Also It should sat Korean Corn Dogs & Lovelies (not & more).

In addition to Corn Dogs, we do sell sweets Up The Lane, it would be great to incorporate these in the walls somehow, please see examples in attachement.

Target Market(s)

Food Markets

Industry/Entity Type

Food

Colors
59FF00
82FF00
B8FF75
E3FFCB
F4FFEA
EE7325
F08F49
F5BC92
FAE3D3
FDF4ED
EB3D1F
EC4F4E
F09395
F8D3D4
FCEDEE

Requirements
Must have
• Cartoon Characters attached
Nice to have
• Stand out design

```html
<!DOCTYPE html>
<html lang="en">
<head>
<meta charset="utf-8">
<title>Up The Lane – Gazebo Branding</title>
<link rel="stylesheet" href="https://fonts.googleapis.com/css2?family=Yellowtail&family=Fredoka:wght@600&display=swap">
<style>
  :root {
    --page: #e4e4e4;
    --red-light: #b3222a;
    --red-mid: #8a1418;
    --red-dark: #3e0709;
    --brand-gold: #f6b21c;
    --wave-orange: #f89b05;
    --wave-edge: #8a3a06;
    --script-white: #ffffff;
    --art-char: #b8742a;
    --art-sweet: #6b3b22;
    --art-sweet-light: #c9a48a;
  }
  html, body {
    margin: 0;
    padding: 0;
    width: 1200px;
    height: 1200px;
    overflow: hidden;
    background: var(--page);
  }
  .gazebo-layout {
    position: relative;
    width: 1200px;
    height: 1200px;
  }
  .panel {
    position: absolute;
    left: 240px;
    width: 720px;
    display: block;
  }
  .canopy-roof { top: 20px; height: 370px; }
  .canopy-valance { top: 400px; height: 80px; }
  .full-wall { top: 490px; height: 465px; }
  .half-wall { top: 965px; height: 215px; }
  .script {
    font-family: "Yellowtail", cursive;
    fill: var(--script-white);
  }
  .brand-name {
    font-family: "Fredoka", sans-serif;
    font-weight: 600;
    fill: var(--brand-gold);
  }
</style>
</head>
<body>
<main class="gazebo-layout">

  <svg class="panel canopy-roof" viewBox="0 0 720 370" aria-label="Canopy roof panel">
    <defs>
      <radialGradient id="roofRed" cx="0.5" cy="0.35" r="0.7">
        <stop offset="0" stop-color="var(--red-light)"/>
        <stop offset="0.6" stop-color="var(--red-mid)"/>
        <stop offset="1" stop-color="var(--red-dark)"/>
      </radialGradient>
    </defs>
    <polygon points="360,0 720,355 720,370 0,370 0,355" fill="url(#roofRed)"/>
    <rect x="205" y="172" width="90" height="105" rx="26" fill="var(--art-char)" role="img" aria-label="Cartoon corn dog and cake characters"/>
    <text class="brand-name" x="305" y="240" font-size="40" textLength="215" lengthAdjust="spacingAndGlyphs">Up The Lane</text>
  </svg>

  <svg class="panel canopy-valance" viewBox="0 0 720 80" aria-label="Canopy valance">
    <defs>
      <linearGradient id="valanceRed" x1="0" y1="0" x2="1" y2="0">
        <stop offset="0" stop-color="var(--red-dark)"/>
        <stop offset="0.35" stop-color="var(--red-mid)"/>
        <stop offset="0.7" stop-color="var(--red-light)"/>
        <stop offset="1" stop-color="var(--red-dark)"/>
      </linearGradient>
    </defs>
    <rect width="720" height="80" fill="url(#valanceRed)"/>
    <text class="script" x="185" y="36" font-size="30" text-anchor="middle">Korean Corn Dogs</text>
    <text class="script" x="185" y="66" font-size="30" text-anchor="middle">&amp; Lovelies</text>
    <rect x="490" y="16" width="48" height="52" rx="14" fill="var(--art-char)" role="img" aria-label="Cartoon corn dog and cake characters"/>
    <text class="brand-name" x="544" y="52" font-size="24">Up The Lane</text>
  </svg>

  <svg class="panel full-wall" viewBox="0 0 720 465" aria-label="Full back wall">
    <defs>
      <radialGradient id="wallRed" cx="0.45" cy="0.45" r="0.75">
        <stop offset="0" stop-color="var(--red-light)"/>
        <stop offset="0.6" stop-color="var(--red-mid)"/>
        <stop offset="1" stop-color="var(--red-dark)"/>
      </radialGradient>
      <linearGradient id="sweetsTone" x1="0" y1="0" x2="0" y2="1">
        <stop offset="0" stop-color="var(--art-sweet)"/>
        <stop offset="0.7" stop-color="var(--art-sweet-light)"/>
        <stop offset="1" stop-color="#e8b9a0"/>
      </linearGradient>
    </defs>
    <rect width="720" height="465" fill="url(#wallRed)"/>
    <rect x="450" y="20" width="250" height="400" rx="40" fill="url(#sweetsTone)" role="img" aria-label="Hand holding chocolate-dipped sweets on sticks"/>
    <rect x="55" y="70" width="115" height="125" rx="30" fill="var(--art-char)" role="img" aria-label="Cartoon corn dog and cake characters"/>
    <text class="brand-name" x="180" y="150" font-size="42" textLength="240" lengthAdjust="spacingAndGlyphs">Up The Lane</text>
    <text class="script" x="180" y="245" font-size="48" text-anchor="middle">Korean</text>
    <text class="script" x="200" y="295" font-size="48" text-anchor="middle">Corn Dogs &amp;</text>
    <text class="script" x="185" y="345" font-size="48" text-anchor="middle">Lovelies</text>
    <path d="M0,410 C70,395 120,420 190,405 S320,392 400,412 S560,398 720,395 L720,465 L0,465 Z" fill="var(--wave-orange)" stroke="var(--wave-edge)" stroke-width="3"/>
  </svg>

  <svg class="panel half-wall" viewBox="0 0 720 215" aria-label="Half wall">
    <defs>
      <linearGradient id="halfRed" x1="0" y1="0" x2="1" y2="1">
        <stop offset="0" stop-color="var(--red-mid)"/>
        <stop offset="0.5" stop-color="var(--red-light)"/>
        <stop offset="1" stop-color="var(--red-dark)"/>
      </linearGradient>
    </defs>
    <rect width="720" height="215" fill="url(#halfRed)"/>
    <rect x="505" y="20" width="150" height="170" rx="25" fill="url(#sweetsTone)" role="img" aria-label="Hand holding chocolate-dipped sweets on sticks"/>
    <rect x="115" y="24" width="58" height="62" rx="16" fill="var(--art-char)" role="img" aria-label="Cartoon corn dog and cake characters"/>
    <text class="brand-name" x="180" y="64" font-size="26">Up The Lane</text>
    <text class="script" x="180" y="122" font-size="30" text-anchor="middle">Korean</text>
    <text class="script" x="180" y="152" font-size="30" text-anchor="middle">Corn Dogs &amp; Lovelies</text>
    <path d="M0,195 C80,188 150,200 230,190 S400,186 480,196 S620,188 720,190 L720,215 L0,215 Z" fill="var(--wave-orange)" stroke="var(--wave-edge)" stroke-width="2"/>
  </svg>

</main>
</body>
</html>
```